Soy Candle Labels

We sell soy candles in recycled wine bottles. The wine bottle is cut in half and filled with pure and natural soy wax and scented with essential oils.
Our product represents good use of up cycling materials for a better use. The product is all natural and eco friendly.
You can see good use of labels and branding for a company in America that does the same thing http://larkmeadow7wicks.example/
Trya dn keep the label uncomplicated like the above labels.
We will need an area to hand stamp the scent. Similar to the labels used on the above website.
We would prefer to use a white or off white paper label with gold or bronze printing - limit the use of colour and keep the label simple and sophisticated.
Emberlace Candle Co. is our company name. Emberlace being the predominant name and candle co. written small underneath right justified.
Die cut labels might look better than a rectangle.
Dimensions should be 90mm Wide x 90mm High
The final design should communicate a professional and quality product. But stay modern and professional. Clean, elegant and sophisticated.
Can use wording such as: Hand Poured, Premium Soy Wax, All Natural, Up cycled
Have a look at the attached image for the look and feel we are going for.
Updates
Designers are having a little bit of trouble interpreting the brief into a viable design. To assist perhaps you can look at WINE LABELS on google images. Design your label around an existing style wine label to give the canld ethe feel of being a bottle of wine. Get creative! :)
Reason: We require more designs. We havnt quite got what were looking for.
Please see brief.

```html
<!DOCTYPE html>
<html lang="en">
<head>
<meta charset="utf-8">
<title>Emberlace Candle Co. – Soy Candle Label</title>
<link rel="stylesheet" href="https://fonts.googleapis.com/css2?family=Saira:wght@300;400&family=Saira+Extra+Condensed:wght@500&family=Open+Sans:wght@400&display=swap">
<style>
  :root {
    --backdrop: #a98733;
    --paper: #fdfcf7;
    --ink: #3a1a0e;
  }
  html, body {
    margin: 0;
    padding: 0;
    width: 1200px;
    height: 1000px;
    overflow: hidden;
    background: var(--backdrop);
  }
  .canvas {
    position: relative;
    width: 1200px;
    height: 1000px;
  }
  .label {
    position: absolute;
    left: 148px;
    top: 62px;
    width: 892px;
    height: 892px;
    background: var(--paper);
    border-radius: 20px;
    overflow: hidden;
    color: var(--ink);
  }
  .label__band {
    position: absolute;
    left: 0; top: 0;
    width: 100%;
    height: 34px;
    background: var(--ink);
  }
  .claims {
    position: absolute;
    left: 44px;
    top: 64px;
    font-family: "Saira", sans-serif;
    font-weight: 400;
    line-height: 1;
  }
  .claims__headline { font-size: 40px; margin: 0 0 14px; }
  .claims__sub { font-size: 28px; margin: 0 0 12px; }
  .claims__detail { font-size: 25px; margin: 0; }
  .scent-stamp {
    position: absolute;
    right: 52px;
    top: 70px;
    font-family: "Saira", sans-serif;
    font-size: 25px;
    line-height: 1;
    writing-mode: vertical-rl;
    text-orientation: upright;
    letter-spacing: 6px;
  }
  .brand {
    position: absolute;
    right: 44px;
    top: 408px;
    text-align: right;
    font-family: "Saira", sans-serif;
    font-weight: 300;
  }
  .brand__name {
    font-size: 112px;
    line-height: 1;
    margin: 0;
    letter-spacing: 1px;
  }
  .brand__tagline {
    font-family: "Saira", sans-serif;
    font-weight: 300;
    font-size: 30px;
    line-height: 1;
    margin: 20px 30px 0 0;
  }
  .footer {
    position: absolute;
    left: 44px;
    right: 43px;
    bottom: 60px;
    display: flex;
    justify-content: space-between;
    font-family: "Saira Extra Condensed", sans-serif;
    font-weight: 500;
    font-size: 50px;
    line-height: 1;
  }
</style>
</head>
<body>
<div class="canvas">
  <article class="label">
    <div class="label__band"></div>

    <section class="claims">
      <p class="claims__headline">Hand Poured</p>
      <p class="claims__sub">All Natural Soy</p>
      <p class="claims__detail">320 gm of Premium Soy Wax</p>
    </section>

    <div class="scent-stamp">SCENT</div>

    <header class="brand">
      <h1 class="brand__name">Emberlace</h1>
      <p class="brand__tagline">Candle Co.</p>
    </header>

    <footer class="footer">
      <span class="footer__origin">Product of Australia</span>
      <span class="footer__material">Up-Cycled wine bottle</span>
    </footer>
  </article>
</div>
</body>
</html>
```